USA Home and Kitchen "Multi-Product" Brand Needs a Stunning Packaging Design.

We need a new packaging design for our Brand: Larkspur Kitchenworks. We Manufacture, Market, and Sell Home & Kitchen Products (Such as Kitchen Utensils and Home Decor to name a few) Direct to Consumers in the United States via our Website and Vendorly.com. We would like to see designs that are simple, clean, and modern, yet stand out and demand attention. Our Preferred colors of the design should include: Black or Grey as the base color/shade), White or Grey for the text, and some additional color can be used for complementary elements/visuals at your own discretion or creativity. We would like this to be an Interchangeable Design that can be easily modified and implemented across all of our other products (i.e: does not contain too many images or design elements that reference a particular product.

Although this design and the concept as a whole is intended to be used across our entire catalogue of products. Please feel free to base your design on our one of our top selling products as per the following URL: https://www.vendorly-example.com/dp/X93QL7714R?ref=abc_title_dp.

Target Market(s)

Our customers tend come from many areas across the spectrum. But the quintessential Larkspur target customer (the type of person who tends to be our most receptive and loyal customer) is female and part of the Millennials generation, aged in her 30s, and is either working full-time in a white-collar job or on home duties, of which she would have young children, a spouse, or other family members to look after. She’s part of the conventional family life who represent the core of ‘middle America’. She doesn’t mind to splurge every now and again on shopping for items that she wants and/or needs, whilst some of the time she’ll also go out of her way to ‘search for a bargain’. She tends to spend more time in her home and kitchen than the average individual. We recognize that cooking for herself and family, and providing a well furnished and stylish home is part of who she is.

Industry/Entity Type

Retail

Font styles to use
Serif
Sans Serif

Colors

Designer to choose only greyscale colors for use in the design.

Requirements
Must have
• Interchangeable Design (A "Universal" Packaging Design that can be easily modified and adapted for use with a large catalogue of products under our brand).
Nice to have
• Some visual elements that gives our packaging/brand the ability to stand out and be unique/memorable.
Should not have
• Our design should not have too much text. Nor should it be cluttered or overcrowded with too much information or visual elements. And does not contain too many images or design elements that reference a particular product. We believe simplicity is key, and quality over quantity.

```html
<!DOCTYPE html>
<html lang="en">
<head>
<meta charset="utf-8">
<title>Larkspur Kitchenworks – Pie Server Packaging</title>
<link rel="stylesheet" href="https://fonts.googleapis.com/css2?family=Open+Sans:wght@400;600;800&display=swap">
<style>
  :root {
    --bg: #e6e6e6;
    --charcoal: #4b4b4d;
    --charcoal-deep: #3a3a3c;
    --mid-grey: #8a8a8c;
    --soft-grey: #a9a9ab;
    --panel-light: #d9d9da;
    --shell-light: #6f6f71;
    --ink: #1c1c1c;
    --white: #f4f4f4;
    --badge: #111111;
  }
  * { margin: 0; padding: 0; box-sizing: border-box; }
  html, body { width: 1200px; height: 800px; overflow: hidden; }
  body {
    background: var(--bg);
    font-family: "Open Sans", Arial, sans-serif;
    position: relative;
  }
  .packaging { position: absolute; left: 80px; top: 110px; width: 1040px; }

  .face { position: relative; width: 1040px; height: 290px; overflow: hidden; }

  /* shared brand block */
  .brand-block {
    position: absolute; left: 0; top: 0; width: 230px; height: 100%;
    background: var(--charcoal-deep);
    display: flex; flex-direction: column; justify-content: center; align-items: center; gap: 16px;
  }
  .brand-mark { width: 18px; height: 18px; border-radius: 50%; background: var(--white); }
  .brand-name {
    color: var(--white); font-weight: 400; font-size: 19px; line-height: 1.4;
    text-align: center; letter-spacing: 3px; text-transform: uppercase;
  }

  /* top face */
  .face--title { background: var(--charcoal); }
  .title-highlight {
    position: absolute; left: 560px; top: 0; width: 240px; height: 290px;
    background: var(--mid-grey); opacity: .55;
  }
  .shell-large {
    position: absolute; left: 830px; top: 35px; width: 220px; height: 220px;
  }
  .title-group { position: absolute; left: 290px; top: 92px; }
  .product-title {
    color: var(--white); font-weight: 800; font-size: 70px; line-height: 1; letter-spacing: 1px;
    white-space: nowrap;
  }
  .product-subtitle {
    color: var(--white); font-weight: 600; font-size: 25px; margin-top: 16px; letter-spacing: .5px;
  }

  /* front face */
  .face--features { background: var(--panel-light); }
  .face--features .brand-block { background: var(--charcoal); }
  .feature-list {
    position: absolute; left: 262px; top: 70px; width: 548px;
    list-style: none; display: grid; grid-template-columns: repeat(4, 1fr); gap: 14px;
  }
  .feature { display: flex; flex-direction: column; gap: 8px; }
  .feature-tick { width: 16px; height: 16px; }
  .feature-heading {
    font-weight: 800; font-size: 13px; line-height: 1.2; color: var(--ink); text-transform: uppercase;
  }
  .feature-text { font-size: 11px; line-height: 1.45; color: var(--ink); margin-top: 4px; }
  .shell-small {
    position: absolute; left: 835px; top: 80px; width: 130px; height: 130px;
  }
  .badge-strip {
    position: absolute; left: 985px; top: 40px; width: 34px; height: 210px;
    background: var(--badge); border-radius: 5px;
    display: flex; flex-direction: column; align-items: center; justify-content: space-around; padding: 8px 0;
  }
  .badge-shape { width: 18px; height: 18px; background: var(--soft-grey); }
  .badge-shape--round { border-radius: 50%; }
</style>
</head>
<body>
<main class="packaging">

  <section class="face face--title">
    <div class="brand-block">
      <span class="brand-mark"></span>
      <p class="brand-name">Larkspur<br>Kitchenworks</p>
    </div>
    <div class="title-highlight"></div>
    <svg class="shell-large" viewBox="0 0 220 220" role="img" aria-label="Spiral shell illustration">
      <circle cx="110" cy="110" r="109" fill="var(--shell-light)"/>
    </svg>
    <div class="title-group">
      <h1 class="product-title">PIE SERVER</h1>
      <p class="product-subtitle">CUT AND SERVE SPATULA</p>
    </div>
  </section>

  <section class="face face--features">
    <div class="brand-block">
      <span class="brand-mark"></span>
      <p class="brand-name">Larkspur<br>Kitchenworks</p>
    </div>

    <ul class="feature-list">
      <li class="feature">
        <svg class="feature-tick" viewBox="0 0 16 16"><path d="M2 8 L6 14 L14 2" fill="none" stroke="#1c1c1c" stroke-width="3"/></svg>
        <div>
          <h2 class="feature-heading">Multi-Purpose<br>For Any Kitchen</h2>
          <p class="feature-text">Perfect for all things sweet &amp; savoury. From Pies &amp; Cakes to Pizzas &amp; Lasagnas.</p>
        </div>
      </li>
      <li class="feature">
        <svg class="feature-tick" viewBox="0 0 16 16"><path d="M2 8 L6 14 L14 2" fill="none" stroke="#1c1c1c" stroke-width="3"/></svg>
        <div>
          <h2 class="feature-heading">2-in-1 Cut and<br>Serve Design</h2>
          <p class="feature-text">Cut your meal &amp; serve it too. As a Dual-sided Blade &amp; Functional Spatula.</p>
        </div>
      </li>
      <li class="feature">
        <svg class="feature-tick" viewBox="0 0 16 16"><path d="M2 8 L6 14 L14 2" fill="none" stroke="#1c1c1c" stroke-width="3"/></svg>
        <div>
          <h2 class="feature-heading">Amazingly<br>Ergonomic</h2>
          <p class="feature-text">A contoured ABS-Thermoplastic Handle made to fit perfectly in your hand.</p>
        </div>
      </li>
      <li class="feature">
        <svg class="feature-tick" viewBox="0 0 16 16"><path d="M2 8 L6 14 L14 2" fill="none" stroke="#1c1c1c" stroke-width="3"/></svg>
        <div>
          <h2 class="feature-heading">Superior<br>Quality</h2>
          <p class="feature-text">Made with Super-Durable Stainless Steel and a Flawless Mirror-finish built to stand the test of time.</p>
        </div>
      </li>
    </ul>

    <svg class="shell-small" viewBox="0 0 130 130" role="img" aria-label="Small spiral shell illustration">
      <circle cx="65" cy="65" r="64" fill="var(--charcoal)"/>
    </svg>

    <div class="badge-strip">
      <span class="badge-shape badge-shape--round"></span>
      <span class="badge-shape"></span>
      <span class="badge-shape"></span>
      <span class="badge-shape badge-shape--round"></span>
    </div>
  </section>

</main>
</body>
</html>
```